New Business Cards for Tormin Group

We need a new Business Card to compliment our new logo. We are a vibrant design, manufacture and install business providing recreation areas, public parks and Municipal spaces. We want business cards that are classy, modern and clean.

We have recently changed our logo, and are celebrating our 40th anniversary. We want business cards with a new modern design to reflect our status.

Target Market(s)

Customers

Contact Information for Business Card

We need all the details of our 3 offices as per the business card attached. Please disregard the old logo on the business card, the other three files show our new logo.

Requirements
Must have
• All info as per attached business card but with new logo.
Nice to have

```html
<!DOCTYPE html>
<html lang="en">
<head>
<meta charset="utf-8">
<title>Tormin Group – Business Card</title>
<link rel="stylesheet" href="https://fonts.googleapis.com/css2?family=Lato:wght@400;700&family=Roboto:wght@400;500&display=swap">
<style>
  :root {
    --brand-red: #e8323b;
    --ink: #3f3f42;
    --card-white: #ffffff;
    --backdrop: #ebe8e4;
  }
  * { box-sizing: border-box; margin: 0; padding: 0; }
  html, body {
    width: 1200px; height: 900px; overflow: hidden;
    background: var(--backdrop);
    font-family: "Roboto", Arial, sans-serif;
  }
  .canvas { position: relative; width: 1200px; height: 900px; }

  .card {
    position: absolute;
    width: 572px; height: 354px;
    box-shadow: 0 3px 8px rgba(0,0,0,0.25);
  }
  .card--front { left: 329px; top: 71px; background: var(--card-white); }
  .card--back  { left: 330px; top: 460px; background: var(--brand-red); }

  .block { position: absolute; color: var(--ink); font-size: 14px; line-height: 18px; }
  .label { color: var(--brand-red); font-weight: 500; }

  .person { left: 22px; top: 24px; }
  .person__name {
    font-family: "Lato", Arial, sans-serif; font-weight: 700;
    font-size: 22px; line-height: 26px; color: var(--brand-red);
  }
  .person__title { font-size: 14px; margin-bottom: 8px; }

  .office__title {
    font-family: "Lato", Arial, sans-serif; font-weight: 700;
    font-size: 18px; line-height: 22px; color: var(--brand-red);
    margin-bottom: 2px;
  }
  .office--head  { left: 22px;  top: 127px; }
  .office--dubai { left: 22px;  top: 229px; }
  .office--qatar { left: 272px; top: 229px; }

  .brand { position: absolute; display: flex; align-items: center; gap: 14px; }
  .brand__name {
    font-family: "Roboto", Arial, sans-serif; font-weight: 500;
    text-transform: uppercase; letter-spacing: 1px;
  }
  .brand--front { left: 298px; top: 72px; }
  .brand--front .brand__name { font-size: 30px; color: var(--ink); }
  .brand--back { left: 140px; top: 98px; }
  .brand--back .brand__name { font-size: 38px; color: var(--card-white); }

  .card__web {
    position: absolute; left: 0; right: 0; top: 298px;
    text-align: center; color: var(--card-white); font-size: 18px;
  }
</style>
</head>
<body>
<main class="canvas">

  <section class="card card--front">
    <div class="block person">
      <div class="person__name">RAMI KASSAB</div>
      <div class="person__title">Managing Partner</div>
      <div><span class="label">M:</span> +971 (0)50 555 0148</div>
      <div><span class="label">E:</span> rami@tormingroup.com</div>
    </div>

    <div class="brand brand--front">
      <svg width="110" height="110" viewBox="0 0 110 110" aria-hidden="true">
        <circle cx="55" cy="55" r="55" fill="var(--brand-red)"/>
      </svg>
      <span class="brand__name">Tormin Group</span>
    </div>

    <div class="block office office--head">
      <div class="office__title">Head Office</div>
      <div>P.O.Box:30418 Abu Dhabi,U.A.E.</div>
      <div><span class="label">P :</span> +971 (0)2 555 0172</div>
      <div><span class="label">F :</span> +971 (0)2 555 0173</div>
      <div><span class="label">E :</span> sales@tormingroup.com</div>
    </div>

    <div class="block office office--dubai">
      <div class="office__title">Dubai Office</div>
      <div>P.O.Box:481206 Dubai,U.A.E.</div>
      <div><span class="label">P :</span> +971 (0)4 555 0191</div>
      <div><span class="label">F :</span> +971 (0)2 555 0192</div>
      <div><span class="label">E :</span> sales@tormingroup.com</div>
    </div>

    <div class="block office office--qatar">
      <div class="office__title">Qatar Office</div>
      <div>P.O.Box:20734 Doha, Qatar</div>
      <div><span class="label">P :</span> +974 4455 0110</div>
      <div><span class="label">F :</span> +971 4455 0111</div>
      <div><span class="label">E :</span> sales@tormingroup.com</div>
    </div>
  </section>

  <section class="card card--back">
    <div class="brand brand--back">
      <svg width="130" height="130" viewBox="0 0 130 130" aria-hidden="true">
        <circle cx="65" cy="65" r="65" fill="var(--card-white)"/>
      </svg>
      <span class="brand__name">Tormin Group</span>
    </div>
    <div class="card__web">www.tormingroup.com</div>
  </section>

</main>
</body>
</html>
```